Label design for organic saffron, saffron and herbal syrup

We cultivate saffron, Damszen roses, flowers and herbs. We would need a recognizable outfit (label) for our products. Theoretically (and practically) we have "converted" the family coat of arms into a kind of LOGO. I would send this in the attachment. It would be nice if - in one way or another - this LOGO / coat of arms could be used (certainly with other colors). For some time we have played with the idea of changing the second part of the family name "Wallmoser" (in German .... greuth sounds similar to Kraut / herb [English]) .... eg Wallmoser's saffron syrup into the labeling.
Our products are primarily syrups, currently herbal syrup and saffron syrup. Here the first problem arises, the only bottles / caps that are actually approved for syrup filling (hot filling) are appallingly ugly (see attachment), the only possibility of "sprucing up" is to use so-called "shrink sleeves" (here we need a diameter of 31 and a length of about 40), the colors of which are also limited. Besides the syrup, we sell saffron as a spice and various herbal mixtures (see appendix current packaging saffron). Our quantities are small (syrup 200ml-330ml), saffron in the gram range.
We also need quasi the back of the labeling (this should be able to be redefined per charge) .... Batch 1 (with small quantity has eg more of herb xy than the next batch or the saffron syrup with batch xy needs more / less saffron). In addition, we are certified organic (for this reason, the reverse side would also have to contain all the requirements of organic labeling) [see attachment].
We do not really want to address a specific clientele. Maybe just people who want to taste, enjoy, mix drinks, cook .... (and - unfortunately - don't like Corvel syrup :-) and want to pay a bit more, or find our saffron or herbs better than others) .
In summary
- Strong recognition value (possibly inclusion of "coat of arms", color variable ... although I personally don't like yellow that much)
- Saffron syrup (the color of the saffron syrup is yellow / golden-yellow-light orange, in a transparent ugly bottle)
- Herbal syrup (color variable from blue / green / brown / red elements, in transparent ugly bottle)
Saffron and other herbs (very small containers, type of container not yet fixed)
Regarding a potential "style" I can unfortunately give little information. On the one hand, I am in love with minimalism, on the other hand, I find the translucent, cryptic, implied enormously attractive and sometimes even the "overloaded" colorful has its charm. I think that all in all, it just has to be coherent, and then it will be good.
Requirements
Must have
- Integration of Code of Arms, modifiable for different products

```html
<!DOCTYPE html>
<html lang="de">
<head>
<meta charset="utf-8">
<title>Wallmoser Safran Sirup – Etikett</title>
<link rel="stylesheet" href="https://fonts.googleapis.com/css2?family=Lustria&family=Roboto+Condensed:wght@400;700&display=swap">
<style>
  :root {
    --navy: #2d2466;
    --navy-deep: #211a52;
    --gold: #c9a14a;
    --gold-light: #e3c67d;
    --cream: #fdf3d2;
    --white: #ffffff;
    --ink: #2b2b2b;
    --organic: #8cc152;
  }
  html, body {
    margin: 0;
    padding: 0;
    width: 879px;
    height: 1200px;
    overflow: hidden;
    background: var(--white);
  }
  .label {
    position: relative;
    width: 879px;
    height: 1200px;
    background: var(--cream);
    overflow: hidden;
    font-family: "Lustria", Georgia, serif;
  }
  .crown-band {
    position: absolute;
    left: 0; top: 0;
    width: 879px; height: 421px;
    background:
      radial-gradient(circle at 12% 100%, rgba(201,161,74,.55), rgba(201,161,74,0) 45%),
      radial-gradient(circle at 88% 100%, rgba(201,161,74,.55), rgba(201,161,74,0) 45%),
      radial-gradient(circle at 0% 0%, rgba(201,161,74,.35), rgba(201,161,74,0) 35%),
      radial-gradient(circle at 100% 0%, rgba(201,161,74,.35), rgba(201,161,74,0) 35%),
      linear-gradient(180deg, var(--navy), var(--navy-deep));
  }
  .crown-arch {
    position: absolute;
    left: 0; top: 0;
  }
  .brand {
    position: absolute;
    left: 253px; width: 375px;
    top: 110px;
    text-align: center;
  }
  .brand-dot {
    display: block;
    width: 110px; height: 110px;
    margin: 0 auto 60px;
    border-radius: 50%;
    background: var(--navy);
  }
  .brand-name {
    font-size: 58px;
    color: var(--navy);
    line-height: 1;
  }
  .gold-rule {
    position: absolute;
    left: 0; top: 421px;
    width: 879px; height: 10px;
    background: var(--gold);
  }
  .product-tab {
    position: absolute;
    left: 207px; top: 431px;
    width: 413px; height: 345px;
    background: var(--navy);
    border-radius: 0 0 52px 52px;
    box-shadow: inset 0 0 0 4px var(--gold);
    overflow: hidden;
  }
  .product-art {
    position: absolute;
    left: 90px; top: 20px;
    width: 233px; height: 320px;
    background: radial-gradient(ellipse at 50% 40%, rgba(120,110,190,.55), rgba(45,36,102,0) 70%);
  }
  .product-name {
    position: absolute;
    left: 0; right: 0; top: 130px;
    text-align: center;
    color: var(--white);
    font-size: 80px;
    line-height: 84px;
    margin: 0;
    font-weight: 400;
  }
  .legal {
    position: absolute;
    left: 712px; top: 452px;
    width: 440px;
    transform-origin: 0 0;
    transform: translate(80px, 0) rotate(90deg);
    font-family: "Roboto Condensed", Arial, sans-serif;
    font-weight: 700;
    font-size: 15px;
    line-height: 20px;
    color: var(--ink);
  }
  .legal p { margin: 0; }
  .best-before {
    position: absolute;
    left: 718px; top: 918px;
    width: 58px; height: 220px;
  }
  .best-before-text {
    position: absolute;
    left: 0; top: 0;
    width: 220px;
    transform-origin: 0 0;
    transform: translate(0, 220px) rotate(-90deg);
    font-family: "Roboto Condensed", Arial, sans-serif;
    font-weight: 700;
    font-size: 19px;
    line-height: 26px;
    color: var(--ink);
  }
  .best-before-box {
    position: absolute;
    left: 28px; top: 0;
    width: 30px; height: 105px;
    border: 2px solid var(--ink);
    background: var(--white);
  }
  .organic-mark {
    position: absolute;
    left: 350px; top: 930px;
    width: 64px; height: 142px;
    background: var(--organic);
    border-radius: 4px;
  }
  .volume, .ratio {
    position: absolute;
    top: 1094px;
    font-family: "Roboto Condensed", Arial, sans-serif;
    font-weight: 700;
    font-size: 26px;
    color: var(--ink);
  }
  .volume { left: 300px; }
  .ratio { left: 490px; }
</style>
</head>
<body>
<main class="label">
  <div class="crown-band" role="img" aria-label="Navy and gold mandala ornament band"></div>
  <svg class="crown-arch" width="879" height="431" viewBox="0 0 879 431" aria-hidden="true">
    <path d="M232 431 V230 A208 208 0 0 1 648 230 V431 Z" fill="var(--gold)"/>
    <path d="M253 431 V238 A187 187 0 0 1 627 238 V431 Z" fill="var(--white)"/>
  </svg>
  <div class="brand">
    <span class="brand-dot"></span>
    <div class="brand-name">Wallmoser</div>
  </div>
  <div class="gold-rule"></div>

  <section class="product-tab">
    <div class="product-art" role="img" aria-label="Faint saffron crocus illustration"></div>
    <h1 class="product-name">Safran<br>Sirup</h1>
  </section>

  <div class="legal">
    <p>*aus kontrolliert biologischer Landwirtschaft</p>
    <p>Expertly crafted by: Marlin-Wallmoser</p>
    <p>Lindenweg 4, 8350 Feldau</p>
  </div>

  <div class="best-before">
    <div class="best-before-text">Best Before:</div>
    <div class="best-before-box"></div>
  </div>

  <div class="organic-mark" role="img" aria-label="Organic certification badge"></div>
  <div class="volume">200mL</div>
  <div class="ratio">1:7</div>
</main>
</body>
</html>
```